Duct Manufacturing Company new to the industry needs business card and stationary design

we are sheet metal duct manufacturers looking for a business card design to fit my new business logo.
nothing to crazy that will date, but want it to stand out from the crowed.
I'm sure you guys will work it out.

Contact Information for Business Card

Glen Marsh
Director

Address
17 Dorwell St
Carrowick NSW 2719

0438 760 514

Sales@flowbend.com.au

Font styles to use
Other font styles liked:
• BankGothic md bt

Requirements
Nice to have
• Like the idea of corner rounded to match logo
• like to keep colours flowing
• font I like sharp square not rounded

```html
<!DOCTYPE html>
<html lang="en">
<head>
<meta charset="utf-8">
<title>Flowbend Industries – Business Card</title>
<link href="https://fonts.googleapis.com/css2?family=Lato:wght@400;700;900&display=swap" rel="stylesheet">
<style>
  :root {
    --stage: #8e8d8d;
    --brand-blue: #044c98;
    --brand-green: #4c9d3a;
    --card-white: #efefef;
    --ink: #1c1c1c;
    --rule-grey: #8aa0c4;
    --muted-white: #c9d6ea;
  }
  * { box-sizing: border-box; margin: 0; padding: 0; }
  html, body { width: 1200px; height: 900px; overflow: hidden; }
  body {
    background: var(--stage);
    font-family: "Lato", sans-serif;
    position: relative;
  }
  .card {
    position: absolute;
    width: 560px;
    height: 320px;
    border-radius: 22px;
    overflow: hidden;
    box-shadow: 0 4px 10px rgba(0,0,0,0.25);
  }

  /* Back */
  .card-back {
    left: 60px; top: 90px;
    background: var(--brand-blue);
  }
  .card-back .brand {
    position: absolute;
    left: 0; right: 0; top: 112px;
    display: flex; align-items: center; justify-content: center; gap: 14px;
  }
  .brand-dot {
    flex: 0 0 auto;
    width: 26px; height: 26px; border-radius: 50%;
    background: var(--brand-green);
  }
  .card-back .brand-name {
    font-weight: 900; font-size: 32px; letter-spacing: 2px;
    color: var(--brand-green);
  }
  .card-back .web-row {
    position: absolute; left: 40px; right: 40px; bottom: 60px;
    display: flex; align-items: center; gap: 14px;
  }
  .web-row .rule { flex: 1; height: 1px; background: var(--rule-grey); }
  .web-row .web { font-size: 15px; color: var(--muted-white); letter-spacing: 0.5px; }

  /* Front */
  .card-front {
    left: 580px; top: 500px;
    background: var(--card-white);
  }
  .card-front .brand {
    position: absolute; left: 34px; top: 62px;
    display: flex; align-items: center; gap: 10px;
  }
  .card-front .brand-dot { width: 20px; height: 20px; }
  .card-front .brand-name {
    font-weight: 900; font-size: 22px; letter-spacing: 1.5px;
    color: var(--brand-green);
  }
  .person {
    position: absolute; right: 34px; top: 96px; text-align: right;
  }
  .person .name { font-weight: 900; font-size: 24px; color: var(--brand-blue); line-height: 1; }
  .person .role { font-size: 14px; color: var(--ink); margin-top: 8px; }
  .divider {
    position: absolute; left: 34px; right: 110px; top: 128px;
    height: 1.5px; background: var(--brand-blue);
  }
  .contacts {
    position: absolute; left: 34px; top: 214px;
    font-size: 17px; color: var(--ink); line-height: 1.45;
  }
  .contacts li { list-style: none; display: flex; align-items: center; gap: 8px; }
  .contacts svg { width: 14px; height: 14px; fill: var(--brand-blue); }
  .address {
    position: absolute; right: 34px; top: 176px; text-align: right;
    font-size: 15px; color: var(--ink); line-height: 1.45;
  }
  .band {
    position: absolute; left: 0; right: 0; bottom: 0; height: 34px;
    display: flex;
  }
  .band .band-blue {
    flex: 0 0 62%; background: var(--brand-blue);
    display: flex; align-items: center; padding-left: 34px;
    color: #ffffff; font-size: 14px; letter-spacing: 0.4px;
  }
  .band .band-green { flex: 1; background: var(--brand-green); }
</style>
</head>
<body>

  <section class="card card-back">
    <div class="brand">
      <span class="brand-dot"></span>
      <span class="brand-name">FLOWBEND INDUSTRIES</span>
    </div>
    <div class="web-row">
      <span class="rule"></span>
      <span class="web">www.flowbend.com.au</span>
      <span class="rule"></span>
    </div>
  </section>

  <section class="card card-front">
    <div class="brand">
      <span class="brand-dot"></span>
      <span class="brand-name">FLOWBEND INDUSTRIES</span>
    </div>
    <div class="person">
      <div class="name">Glen Marsh</div>
      <div class="role">Director</div>
    </div>
    <div class="divider"></div>
    <ul class="contacts">
      <li>
        <svg viewBox="0 0 24 24" aria-hidden="true"><path d="M6.6 10.8a15 15 0 0 0 6.6 6.6l2.2-2.2a1 1 0 0 1 1-.25 11.4 11.4 0 0 0 3.6.57 1 1 0 0 1 1 1V20a1 1 0 0 1-1 1A17 17 0 0 1 3 4a1 1 0 0 1 1-1h3.5a1 1 0 0 1 1 1c0 1.25.2 2.45.57 3.6a1 1 0 0 1-.25 1z"/></svg>
        0438 760 514
      </li>
      <li>
        <svg viewBox="0 0 24 24" aria-hidden="true"><path d="M2 5h20v14H2z M3.5 6.5 12 13l8.5-6.5v-.01H3.5z" fill-rule="evenodd"/></svg>
        Sales@flowbend.com.au
      </li>
    </ul>
    <div class="address">
      17 Dorwell St<br>
      Carrowick NSW 2719
    </div>
    <div class="band">
      <div class="band-blue">www.flowbend.com.au</div>
      <div class="band-green"></div>
    </div>
  </section>

</body>
</html>
```